Commercial Loan Originator Business Card (CHANGE COLORS SCHEME)

CHANGE COLOR SCHEME - SAME DESIGN

Name Marlene Agate
Title Commercial Loan Originator
Office (800) 417-2906 x68
Direct (240) 615-2043
Email freshgreens4life@quillbox.example

Name Dale Morrow
Office (800) 417-2906 x70
Direct (410) 392-5184
Email d.morthehomeguy@quillbox.example

Name Leonard Vasko
Office (800) 417-2906 x71
Direct (215) 463-0712
Email l.vasko41@quillbox.example

Name Gwen Halsey
Office (800) 417-2906 x
Direct (202) 548-1370
Email ghalsey63@quillbox.example

Name Mirna Ashby
Office (800) 417-2906 x72
Direct (240) 871-4526
Email tristatehomelending@quillbox.example

```html
<!DOCTYPE html>
<html lang="en">
<head>
<meta charset="utf-8">
<title>Mirna Ashby – Commercial Loan Originator</title>
<link rel="stylesheet" href="https://fonts.googleapis.com/css2?family=Cinzel:wght@600&family=Poppins:wght@400&display=swap">
<style>
  :root {
    --page-bg: #8a8a8a;
    --card-bg: #ffffff;
    --accent-main: #0f8a8c;
    --accent-deep: #17324f;
    --ink: #222222;
    --portrait-light: #c9a48e;
    --portrait-dark: #2b2322;
  }
  html, body {
    margin: 0;
    width: 1200px;
    height: 952px;
    overflow: hidden;
    background: var(--page-bg);
  }
  .card-frame {
    position: absolute;
    left: 50px;
    top: 137px;
    width: 1100px;
    height: 679px;
  }
  .card {
    position: absolute;
    left: 0;
    top: 0;
    width: 1053px;
    height: 650px;
    transform: scale(1.0446);
    transform-origin: 0 0;
    background: var(--card-bg);
    border-radius: 36px;
    overflow: hidden;
  }
  .card-art {
    position: absolute;
    inset: 0;
    width: 1053px;
    height: 650px;
  }
  .name-marker {
    position: absolute;
    left: 0;
    top: 90px;
    width: 25px;
    height: 63px;
    background: var(--accent-main);
  }
  .name {
    position: absolute;
    left: 47px;
    top: 80px;
    margin: 0;
    font-family: "Cinzel", serif;
    font-weight: 600;
    font-size: 46px;
    line-height: 1.1;
    letter-spacing: 0.5px;
    color: var(--accent-main);
  }
  .job-title {
    position: absolute;
    left: 49px;
    top: 126px;
    margin: 0;
    font-family: "Poppins", sans-serif;
    font-size: 29px;
    line-height: 1.2;
    color: var(--ink);
  }
  .contact-list {
    position: absolute;
    left: 45px;
    top: 302px;
    margin: 0;
    padding: 0;
    list-style: none;
    font-family: "Poppins", sans-serif;
    font-size: 30px;
    line-height: 39px;
    color: var(--ink);
  }
  .contact-list li {
    display: flex;
    align-items: center;
    white-space: nowrap;
  }
  .contact-icon {
    width: 30px;
    height: 30px;
    margin-right: 16px;
    flex: none;
  }
  .contact-tag {
    color: var(--accent-main);
    margin-left: 18px;
  }
  .email {
    font-size: 25px;
  }
</style>
</head>
<body>
  <div class="card-frame">
    <div class="card">
      <svg class="card-art" viewBox="0 0 1053 650">
        <defs>
          <linearGradient id="portraitTone" x1="0" y1="0" x2="0" y2="1">
            <stop offset="0" stop-color="#ffffff"/>
            <stop offset="0.15" stop-color="var(--portrait-light)"/>
            <stop offset="0.45" stop-color="var(--portrait-dark)"/>
            <stop offset="1" stop-color="var(--portrait-dark)"/>
          </linearGradient>
        </defs>
        <rect class="portrait-area" role="img" aria-label="Portrait photo of the loan originator" x="640" y="60" width="413" height="560" rx="40" fill="url(#portraitTone)"/>
        <path class="wave-deep" d="M0,495 C150,440 360,445 650,568 L650,650 L0,650 Z" fill="var(--accent-deep)"/>
        <path class="wave-main" d="M0,547 C150,490 320,478 520,518 C700,556 860,612 1053,580 L1053,650 L0,650 Z" fill="var(--accent-main)" stroke="#ffffff" stroke-width="6"/>
      </svg>

      <div class="name-marker"></div>
      <h1 class="name">MIRNA ASHBY</h1>
      <p class="job-title">Commercial Loan Originator</p>

      <ul class="contact-list">
        <li>
          <svg class="contact-icon" viewBox="0 0 24 24"><path d="M6.6 10.8a15 15 0 0 0 6.6 6.6l2.2-2.2c.3-.3.7-.4 1-.2 1.1.4 2.3.6 3.6.6.6 0 1 .4 1 1V20c0 .6-.4 1-1 1A17 17 0 0 1 3 4c0-.6.4-1 1-1h3.5c.6 0 1 .4 1 1 0 1.3.2 2.5.6 3.6.1.3 0 .7-.2 1z" fill="none" stroke="var(--accent-main)" stroke-width="2.2"/><path d="M14 3.5a7 7 0 0 1 6.5 6.5M14 7a3.5 3.5 0 0 1 3 3" fill="none" stroke="var(--accent-main)" stroke-width="2"/></svg>
          <span>(800) 417-2906 x72</span>
        </li>
        <li>
          <svg class="contact-icon" viewBox="0 0 24 24"><path d="M6.6 10.8a15 15 0 0 0 6.6 6.6l2.2-2.2c.3-.3.7-.4 1-.2 1.1.4 2.3.6 3.6.6.6 0 1 .4 1 1V20c0 .6-.4 1-1 1A17 17 0 0 1 3 4c0-.6.4-1 1-1h3.5c.6 0 1 .4 1 1 0 1.3.2 2.5.6 3.6.1.3 0 .7-.2 1z" fill="none" stroke="var(--accent-main)" stroke-width="2.2"/><path d="M14 3.5a7 7 0 0 1 6.5 6.5M14 7a3.5 3.5 0 0 1 3 3" fill="none" stroke="var(--accent-main)" stroke-width="2"/></svg>
          <span>(240) 871-4526</span><span class="contact-tag">(Direct )</span>
        </li>
        <li>
          <svg class="contact-icon" viewBox="0 0 24 24"><rect x="1" y="5" width="22" height="14" fill="var(--accent-main)"/><path d="M1 5l11 8 11-8M1 19l8-7M23 19l-8-7" fill="none" stroke="#ffffff" stroke-width="1.5"/></svg>
          <span class="email">tristatehomelending@quillbox.example</span>
        </li>
      </ul>
    </div>
  </div>
</body>
</html>
```